Professional and creative business card design for recruiting service providers

Our company supports German medium-sized companies in filling vacancies promptly. For this we use social media marketing and bring our customers into the visibility.

We want a professional but also creative design for our business cards.

Please look at lindqvar-staff.de to get an impression of our CI.

Target Market(s)

Small and medium-sized companies in Germany from the industry

Industry/Entity Type

Industrie, Handwerk

Contact Information for Business Card

Name, Position, Telefonnummer, Email, Website

Colors
EE7325
F08F49
F5BC92
FAE3D3
FDF4ED

Requirements
Must have
• A picture of the employee and in the style of www.lindqvar-staff.de

```html
<!DOCTYPE html>
<html lang="de">
<head>
<meta charset="utf-8">
<title>Lindqvar &amp; Staff – Visitenkarten</title>
<link href="https://fonts.googleapis.com/css2?family=Montserrat:wght@500;700;800&family=Arimo:wght@400;700&display=swap" rel="stylesheet">
<style>
  :root {
    --stage: #e8e8e8;
    --paper: #ffffff;
    --brand: #e85b2a;
    --brand-light: #f08f49;
    --ink: #2b2b2e;
    --ink-soft: #3a3a3a;
    --photo-top: #c9c4c0;
    --photo-bottom: #24252b;
  }
  * { margin: 0; padding: 0; box-sizing: border-box; }
  html, body { width: 1200px; height: 802px; overflow: hidden; background: var(--stage); }
  .stage { position: relative; width: 1200px; height: 802px; }

  .card {
    position: absolute; top: 236px; width: 510px; height: 330px;
    border-radius: 4px; overflow: hidden;
    box-shadow: 0 6px 18px rgba(0,0,0,.18);
  }
  .card--front { left: 60px; background: var(--paper); }
  .card--back { left: 630px; background: var(--brand); display: flex; align-items: center; justify-content: center; }

  .card__art { position: absolute; inset: 0; }

  .wordmark { display: flex; align-items: center; gap: 12px; font-family: "Montserrat", sans-serif; font-weight: 800; text-transform: uppercase; line-height: 1.02; }
  .wordmark__square { flex: none; }
  .card--front .wordmark { position: absolute; left: 34px; top: 54px; color: var(--ink); font-size: 23px; letter-spacing: 1px; }
  .card--front .wordmark__square { width: 40px; height: 40px; background: var(--brand); }
  .card--back .wordmark { color: var(--paper); font-size: 38px; letter-spacing: 2px; gap: 22px; }
  .card--back .wordmark__square { width: 64px; height: 64px; border: 6px solid var(--paper); }

  .contact { position: absolute; left: 34px; top: 146px; font-family: "Arimo", sans-serif; color: var(--ink-soft); }
  .contact__name { font-family: "Arimo", sans-serif; font-weight: 700; font-size: 19px; color: var(--brand); letter-spacing: .5px; text-transform: uppercase; }
  .contact__role { font-size: 14px; margin-top: 2px; }
  .contact__address { font-size: 13px; line-height: 1.3; margin-top: 16px; }
  .contact__list { list-style: none; margin-top: 14px; font-size: 13px; line-height: 1.45; }
  .contact__list li { display: flex; align-items: center; gap: 8px; }
  .contact__icon { width: 12px; height: 12px; flex: none; }
</style>
</head>
<body>
<main class="stage">

  <section class="card card--front" aria-label="Visitenkarte Vorderseite">
    <svg class="card__art" viewBox="0 0 510 330" width="510" height="330">
      <defs>
        <linearGradient id="portraitTone" x1="0" y1="0" x2="0" y2="1">
          <stop offset="0" stop-color="var(--photo-top)"/>
          <stop offset="1" stop-color="var(--photo-bottom)"/>
        </linearGradient>
      </defs>
      <rect class="portrait" x="285" y="18" width="215" height="240" fill="url(#portraitTone)" role="img" aria-label="Porträtfoto des Mitarbeiters"/>
      <polygon class="accent-stripe" points="272,330 510,92 510,112 292,330" fill="var(--ink)"/>
      <polygon class="accent-band" points="292,330 510,112 510,330" fill="var(--brand)"/>
      <text class="accent-band__url" x="425" y="245" transform="rotate(-45 425 245)" text-anchor="middle" fill="var(--paper)" font-family="Arimo, sans-serif" font-size="13">www.lindqvar-staff.de</text>
    </svg>

    <div class="wordmark">
      <span class="wordmark__square"></span>
      <span>Lindqvar<br>&amp; Staff</span>
    </div>

    <div class="contact">
      <p class="contact__name">Elias Brandt</p>
      <p class="contact__role">Manager</p>
      <p class="contact__address">Lindenweg 42b<br>70469 Musterstadt</p>
      <ul class="contact__list">
        <li>
          <svg class="contact__icon" viewBox="0 0 12 12" aria-hidden="true"><path d="M3 1 L5 3.5 L4 5 Q5.5 7 7 8 L8.5 7 L11 9 L9.5 11 Q5 10.5 1 3 Z" fill="var(--brand)"/></svg>
          <span>0151 204 7391</span>
        </li>
        <li>
          <svg class="contact__icon" viewBox="0 0 12 12" aria-hidden="true"><rect x="1" y="2.5" width="10" height="7" fill="none" stroke="var(--brand)" stroke-width="1.3"/><path d="M1 2.5 L6 6.5 L11 2.5" fill="none" stroke="var(--brand)" stroke-width="1.3"/></svg>
          <span>info@lindqvar-staff.de</span>
        </li>
      </ul>
    </div>
  </section>

  <section class="card card--back" aria-label="Visitenkarte Rückseite">
    <div class="wordmark">
      <span class="wordmark__square"></span>
      <span>Lindqvar<br>&amp; Staff</span>
    </div>
  </section>

</main>
</body>
</html>
```